Meridale Bed Company Needs Business Card

Looking for a very nice looking business card. Creative but not extravagant. We sell beds and pillows across the U.S. and need something professional but catchy. I have attached the logo.

Name : Devin Holt
Title : President
Phone : (800) 471-2960
Email: sleep@quilmora.com
Website: www.quilmora.com

Can be single-sided or double-sided
horizontal or vertical

Can use Blues/Greys

Target Market(s)

Mass Market

Industry/Entity Type

Retail

Contact Information for Business Card

Name : Devin Holt
Title : President
Phone : (800) 471-2960
Email: sleep@quilmora.com
Website: www.quilmora.com

Requirements
Must have
• Clean, Modern, Smooth
• Can use Blues/Greys
• On the other side without the information - have something simple like www.quilmora.com or our logo
Nice to have
• Surprise me
Should not have
• Nothing crazy, nothing cluttered

```html
<!DOCTYPE html>
<html lang="en">
<head>
<meta charset="utf-8">
<title>Quilmora Business Card</title>
<link href="https://fonts.googleapis.com/css2?family=Arimo:wght@400;700&display=swap" rel="stylesheet">
<style>
  :root {
    --backdrop: #2b2c2e;
    --card-white: #ffffff;
    --card-grey: #555759;
    --card-grey-dark: #434547;
    --brand-blue: #2ea3d9;
    --brand-blue-light: #4bb4e3;
    --pattern-tint: #e7f2f9;
    --pattern-tint-soft: #f4f9fc;
    --text-on-blue: #ffffff;
  }
  * { margin: 0; padding: 0; box-sizing: border-box; }
  html, body {
    width: 1200px;
    height: 843px;
    overflow: hidden;
    background: var(--backdrop);
    font-family: "Arimo", Arial, sans-serif;
  }
  .canvas {
    position: relative;
    width: 1200px;
    height: 843px;
  }
  .card {
    position: absolute;
    top: 272px;
    width: 525px;
    height: 300px;
    overflow: hidden;
    box-shadow: 0 14px 30px rgba(0, 0, 0, 0.45);
  }
  /* Back of card: logo side */
  .card-back {
    left: 55px;
    background: linear-gradient(135deg, var(--card-grey) 0%, var(--card-grey-dark) 100%);
    display: flex;
    align-items: center;
    justify-content: center;
  }
  .brand-name {
    color: var(--brand-blue-light);
    font-weight: 400;
    font-size: 64px;
    letter-spacing: 3px;
  }
  /* Front of card: contact side */
  .card-front {
    left: 620px;
    background: var(--card-white);
  }
  .pattern-area {
    position: absolute;
    left: 0;
    width: 100%;
    background: linear-gradient(180deg, var(--pattern-tint-soft) 0%, var(--pattern-tint) 50%, var(--pattern-tint-soft) 100%);
  }
  .pattern-top { top: 0; height: 70px; }
  .pattern-bottom { top: 186px; height: 114px; }
  .contact-band {
    position: absolute;
    left: 0;
    top: 70px;
    width: 100%;
    height: 116px;
    background: linear-gradient(180deg, var(--brand-blue-light) 0%, var(--brand-blue) 100%);
    color: var(--text-on-blue);
    padding: 24px 0 0 190px;
  }
  .contact-name {
    font-size: 19px;
    font-weight: 700;
    margin-bottom: 9px;
  }
  .contact-title {
    font-weight: 400;
    font-size: 16px;
  }
  .contact-line {
    font-size: 13px;
    line-height: 20px;
  }
  .contact-label { font-weight: 700; }
  .contact-gap { display: inline-block; width: 12px; }
  .contact-web {
    letter-spacing: 2.2px;
    padding-left: 44px;
  }
</style>
</head>
<body>
  <main class="canvas">
    <section class="card card-back">
      <span class="brand-name">quilmora</span>
    </section>

    <section class="card card-front">
      <div class="pattern-area pattern-top" role="img" aria-label="Faint repeated brand name pattern in pale blue"></div>
      <div class="contact-band">
        <p class="contact-name">Devin Holt - <span class="contact-title">President</span></p>
        <p class="contact-line"><span class="contact-label">P:</span> (800) 471-2960<span class="contact-gap"></span><span class="contact-label">E:</span> sleep@quilmora.com</p>
        <p class="contact-line contact-web">www.quilmora.com</p>
      </div>
      <div class="pattern-area pattern-bottom" role="img" aria-label="Faint repeated brand name pattern in pale blue"></div>
    </section>
  </main>
</body>
</html>
```